Quorva - corporate Business Card

We need a good look and innovative business card for a new start up company based in Los Angeles called "Quorva". We are in a payment business, including payment card, app, and ewallet. We are expert in online payment and Card not present (CNP) transaction.
We need an innovative, modern business card.

Our logo font is Aero Matics

Target Market(s)

Startup - Bank - Online Payment - Card Manufacturing

Industry/Entity Type

Startup

Contact Information for Business Card

phone: 555 014 7396 - Address: 4172 Marlowe blvd, Brenmoor, CA 90299

Requirements
Must have
• Message: innovative, professional, expert, high tech, trust, online payment expert, security
Nice to have
• no comment
Should not have
• no Comment

```html
<!DOCTYPE html>
<html lang="en">
<head>
<meta charset="utf-8">
<title>Quorva – Business Card</title>
<link href="https://fonts.googleapis.com/css2?family=Exo+2:wght@400;500;600&display=swap" rel="stylesheet">
<style>
  :root {
    --backdrop: #5b5b5b;
    --card-dark: #0d0d0d;
    --brand-red: #c22332;
    --brand-red-deep: #b21f2d;
    --text-light: #f2f2f2;
    --disc-white: #fbfbfb;
  }
  * { margin: 0; padding: 0; box-sizing: border-box; }
  html, body {
    width: 1200px; height: 900px; overflow: hidden;
    background: var(--backdrop);
    font-family: "Exo 2", "Segoe UI", sans-serif;
  }
  .stage { position: relative; width: 1200px; height: 900px; }

  .card { position: absolute; top: 192px; width: 302px; height: 491px; }

  .card-front {
    left: 295px;
    background: var(--card-dark);
    border-radius: 0 14px 14px 0;
    color: var(--text-light);
    text-align: center;
  }
  .brand {
    position: absolute; left: 27px; top: 88px;
    display: flex; align-items: center; gap: 8px;
  }
  .brand-dot {
    width: 74px; height: 74px; border-radius: 50%;
    background: var(--brand-red);
  }
  .brand-name {
    font-size: 47px; font-weight: 500; color: var(--brand-red);
    letter-spacing: 1px; line-height: 1;
  }
  .contact { position: absolute; left: 0; right: 0; top: 263px; }
  .person-name {
    font-size: 26px; font-weight: 600; color: var(--brand-red);
    letter-spacing: 0.5px; line-height: 28px;
  }
  .person-role { font-size: 15px; line-height: 18px; }
  .divider {
    width: 130px; height: 1px;
    background: linear-gradient(90deg, transparent, var(--brand-red), transparent);
  }
  .divider-top { margin: 8px auto 9px; }
  .divider-bottom { margin: 7px auto 6px; }
  .contact-line { font-size: 14px; line-height: 20px; }
  .address { font-size: 14px; line-height: 18px; }

  .card-back {
    left: 621px; width: 305px;
    border-radius: 14px;
    background: radial-gradient(circle at 50% 50%, var(--brand-red-deep) 0%, var(--brand-red) 75%);
  }
  .back-disc {
    position: absolute; left: 75px; top: 168px;
    width: 156px; height: 156px; border-radius: 50%;
    background: var(--disc-white);
    border: 1px solid #7a2a30;
    box-shadow: 0 1px 3px rgba(0,0,0,0.3);
    display: flex; align-items: center; justify-content: center;
  }
  .back-disc-name {
    font-size: 30px; font-weight: 500; color: var(--brand-red);
    letter-spacing: 1px;
  }
</style>
</head>
<body>
  <main class="stage">
    <section class="card card-front">
      <div class="brand">
        <span class="brand-dot"></span>
        <span class="brand-name">quorva</span>
      </div>
      <div class="contact">
        <p class="person-name">Marek Dalton</p>
        <p class="person-role">Director</p>
        <div class="divider divider-top"></div>
        <p class="contact-line">555 014 7396</p>
        <p class="contact-line">www.quorva.com</p>
        <div class="divider divider-bottom"></div>
        <p class="address">4172 Marlowe blvd,<br>Brenmoor, CA 90299</p>
      </div>
    </section>

    <section class="card card-back">
      <div class="back-disc">
        <span class="back-disc-name">quorva</span>
      </div>
    </section>
  </main>
</body>
</html>
```